Interior Design/ New Construction interior finishes

Interior Design Website

Target Market(s)

Home builders, New Construction, Renovations, Public

Industry/Entity Type

Construction

Coding

Coded - Design and coding required

Number of Pages Required

1 page

Font styles to use
Sans Serif

Colors

Designer to choose colors to be used in the design.

Requirements
Must have
• Section to upload pictures of projects
• Simple and modern design
• Designer 1 details about myself
• Logo
• Upload section for photos for future jobs
Nice to have
• Sections they can click on to see certain rooms in a house
• Decorating, floral arrangements, holiday decorating.
• I have lots of before and after as well. Maybe a section for those.

```html
<!DOCTYPE html>
<html lang="en">
<head>
<meta charset="utf-8">
<title>Marlow Designs – Custom Home Building &amp; Remodeling</title>
<link href="https://fonts.googleapis.com/css2?family=Roboto:ital,wght@0,300;0,400;0,500;0,700;1,400&display=swap" rel="stylesheet">
<style>
:root{
  --ink:#1d1d1d;
  --text:#444;
  --muted:#666;
  --white:#fff;
  --dark:#151515;
  --band:#ececec;
  --line:#cfcfcf;
  --hero-a:#3e3a36;
  --hero-b:#8a8078;
  --accent:#222;
}
*{box-sizing:border-box;margin:0;padding:0}
html,body{width:1200px;height:3636px;overflow:hidden}
body{font-family:"Roboto",Arial,sans-serif;color:var(--text);background:var(--white);position:relative}
.abs{position:absolute}
.photo{position:absolute}

/* header / hero */
.hero{position:absolute;left:0;top:0;width:1200px;height:620px;background:linear-gradient(160deg,var(--hero-b) 0%,var(--hero-a) 55%,#5d554e 100%)}
.hero-shade{position:absolute;inset:0;background:rgba(0,0,0,.28)}
.nav{position:absolute;left:98px;top:38px;display:flex;gap:42px}
.nav a{color:var(--white);font-size:14px;font-weight:500;text-decoration:none;letter-spacing:.3px}
.nav-rule{position:absolute;left:98px;top:90px;width:1004px;height:1px;background:rgba(255,255,255,.45)}
.social-top{position:absolute;right:98px;top:40px;display:flex;gap:12px}
.social-top span{width:13px;height:13px;border-radius:50%;background:var(--white);opacity:.9}
.brand-mark{position:absolute;left:532px;top:174px;width:136px;height:136px;border:4px solid var(--white);border-radius:50%}
.brand-name{position:absolute;left:0;width:1200px;top:322px;text-align:center;color:var(--white);font-size:40px;font-weight:400;letter-spacing:3px}
.hero-title{position:absolute;left:0;width:1200px;top:388px;text-align:center;color:var(--white);font-size:58px;font-weight:700;line-height:1}
.hero-sub{position:absolute;left:0;width:1200px;top:450px;text-align:center;color:var(--white);font-size:42px;font-weight:700;line-height:1}
.arrow{position:absolute;width:30px;height:30px;border-radius:50%;background:rgba(20,20,20,.75)}
.arrow svg{position:absolute;left:9px;top:8px}

/* service cards */
.card{position:absolute;top:625px;height:337px;overflow:hidden}
.card-shade{position:absolute;left:0;right:0;bottom:0;height:142px;background:rgba(0,0,0,.55)}
.card h3{position:absolute;left:0;right:0;top:210px;text-align:center;color:var(--white);font-size:23px;font-weight:500}
.card p{position:absolute;left:40px;right:40px;top:247px;text-align:center;color:var(--white);font-size:13px;line-height:19px}
.card .btn{position:absolute;left:50%;margin-left:-55px;top:297px;width:110px;height:30px;border:1.5px solid var(--white);border-radius:15px;color:var(--white);font-size:13px;text-align:center;line-height:27px}

/* welcome */
.section-title{position:absolute;left:0;width:1200px;text-align:center;color:var(--ink);font-size:31px;font-weight:500}
.title-rule{position:absolute;left:565px;width:70px;height:3px;background:var(--ink)}
.welcome-text{position:absolute;left:128px;width:944px;top:1088px;text-align:center;font-size:13.5px;line-height:25px;color:var(--text)}
.feature{position:absolute;top:1211px;width:240px;text-align:center}
.feature .ring{width:110px;height:110px;margin:0 auto;border:3px solid #333;border-radius:50%;position:relative}
.feature .ring svg{position:absolute;left:29px;top:28px}
.feature h4{margin-top:27px;font-size:20px;font-weight:500;color:var(--ink)}
.feature p{margin-top:10px;font-size:13.5px;line-height:22px;padding:0 12px}

/* project grid */
.tile-caption{position:absolute;left:414px;top:1636px;width:372px;height:247px;background:rgba(60,60,60,.85)}
.tile-caption p{position:absolute;left:0;right:0;top:92px;text-align:center;color:var(--white);font-size:15px;line-height:22px}
.tile-caption svg{position:absolute;left:173px;top:152px}

/* testimonial */
.quote{position:absolute;left:190px;width:820px;top:2352px;text-align:center;font-style:italic;font-size:14.5px;line-height:25px;color:var(--text)}
.quote-by{position:absolute;left:0;width:1200px;top:2443px;text-align:center;font-style:italic;font-weight:500;font-size:15px;color:var(--ink)}
.dots{position:absolute;left:561px;top:2500px;display:flex;gap:5px}
.dots span{width:23px;height:3px;background:#bbb}
.dots span.on{background:#444}

/* before after */
.ba{position:absolute;left:0;top:2584px;width:1200px;height:630px;background:linear-gradient(180deg,#232323,#0f0f0f)}
.ba-frame{position:absolute;top:2749px;height:378px;border:3px solid var(--white)}
.ba-tag{position:absolute;bottom:14px;left:6px;background:var(--white);color:var(--ink);font-size:11px;font-weight:500;padding:5px 10px}

/* contact band */
.contact{position:absolute;left:0;top:3214px;width:1200px;height:330px;background:var(--band)}
.col-title{position:absolute;top:3268px;font-size:24px;font-weight:700;color:var(--ink)}
.info{position:absolute;left:97px;font-size:13px;line-height:20px;color:#333}
.info svg{position:absolute;left:0;top:3px}
.info div{padding-left:28px}
.field{position:absolute;width:228px;height:42px;border:1px solid var(--line);background:var(--white);font-size:12px;color:#333;padding:12px 12px}
.submit{position:absolute;left:417px;top:3440px;width:228px;height:42px;background:var(--accent);color:var(--white);font-size:16px;font-weight:700;text-align:center;line-height:42px}
.links{position:absolute;left:948px;top:3330px;list-style:none}
.links li{font-size:13px;color:#333;line-height:25.7px;padding-left:20px;position:relative}
.links li::before{content:"›";position:absolute;left:0;top:0;color:#555}

/* footer */
.foot-mark{position:absolute;left:97px;top:3572px;width:46px;height:46px;border:2px solid #333;border-radius:50%}
.copy{position:absolute;left:0;width:1200px;top:3588px;text-align:center;font-size:13px;color:#333}
.social-foot{position:absolute;left:998px;top:3585px;display:flex;gap:6px}
.social-foot span{width:20px;height:20px;border:1.5px solid #444;border-radius:50%}
</style>
</head>
<body>

<header class="hero">
  <div class="photo" role="img" aria-label="Photo of a remodeled master bathroom with freestanding tub and chandelier" style="inset:0;background:linear-gradient(160deg,#9a9088 0%,#4a443f 50%,#6d645c 100%)"></div>
  <div class="hero-shade"></div>
  <nav class="nav">
    <a href="#">HOME</a><a href="#">ABOUT US</a><a href="#">SERVICES</a><a href="#">PROJECTS</a><a href="#">PROPERTY MANAGEMENT</a><a href="#">CONTACT US</a>
  </nav>
  <div class="social-top"><span></span><span></span><span></span><span></span><span></span><span></span></div>
  <div class="nav-rule"></div>
  <div class="brand-mark"></div>
  <div class="brand-name">Marlow Designs</div>
  <h1 class="hero-title">CUSTOM HOME</h1>
  <div class="hero-sub">BUILDING &amp; REMODELING</div>
  <div class="arrow" style="left:38px;top:290px"><svg width="12" height="14" viewBox="0 0 12 14"><path d="M9 1 3 7l6 6" stroke="#fff" stroke-width="2.2" fill="none"/></svg></div>
  <div class="arrow" style="left:1134px;top:290px"><svg width="12" height="14" viewBox="0 0 12 14"><path d="M3 1l6 6-6 6" stroke="#fff" stroke-width="2.2" fill="none"/></svg></div>
</header>

<section class="card" style="left:0;width:396px">
  <div class="photo" role="img" aria-label="Photo of a decorated living room with fireplace" style="inset:0;background:linear-gradient(150deg,#7c5a3c,#c49a6a 50%,#5a3e2a)"></div>
  <div class="card-shade"></div>
  <h3>Decorating</h3>
  <p>Sed ut perspiciatis unde omnis iste natus error sit voluptatem accusantium doloremque</p>
  <div class="btn">Read More ›</div>
</section>
<section class="card" style="left:402px;width:398px">
  <div class="photo" role="img" aria-label="Photo of a bright sitting room with floral arrangement" style="inset:0;background:linear-gradient(150deg,#d9d4cc,#f1eee9 50%,#9c958c)"></div>
  <div class="card-shade"></div>
  <h3>Floral Arrangements</h3>
  <p>Sed ut perspiciatis unde omnis iste natus error sit voluptatem accusantium doloremque</p>
  <div class="btn">Read More ›</div>
</section>
<section class="card" style="left:805px;width:395px">
  <div class="photo" role="img" aria-label="Photo of a holiday decorated wall with stockings and tree" style="inset:0;background:linear-gradient(150deg,#8f8a86,#b7b1ab 55%,#6e3a34)"></div>
  <div class="card-shade"></div>
  <h3>Holiday Decorating</h3>
  <p>Sed ut perspiciatis unde omnis iste natus error sit voluptatem accusantium doloremque</p>
  <div class="btn">Read More ›</div>
</section>

<h2 class="section-title" style="top:1036px">WELCOME TO MARLOW DESIGNS</h2>
<p class="welcome-text">Sed ut perspiciatis unde omnis iste natus error sit voluptatem accusantium doloremque laudantium, totam rem aperiam, eaque ipsa quae ab illo inventore veritatis et quasi architecto beatae vitae dicta sunt explicabo. Nemo enim ipsam voluptatem quia voluptas sit aspernatur aut odit aut fugit, sed quia consequuntur magni dolores eos qui ratione voluptatem sequi nesciunt. Neque porro quisquam doloremque laudantium, totam rem aperiam</p>

<div class="feature" style="left:88px">
  <div class="ring"><svg width="52" height="52" viewBox="0 0 52 52" fill="none" stroke="#333" stroke-width="2.5"><rect x="6" y="6" width="34" height="40"/><path d="M12 16h14M12 24h10M30 34l16-22"/></svg></div>
  <h4>Remodeling</h4>
  <p>Sed ut perspiciatis unde omnis iste natus error sit voluptatem santium doloremque laudantium</p>
</div>
<div class="feature" style="left:345px">
  <div class="ring"><svg width="52" height="52" viewBox="0 0 52 52" fill="none" stroke="#333" stroke-width="2.5"><path d="M6 46V20l10-8 10 8v26M26 46V14l10-8 10 8v32M4 46h44M12 26h8M12 34h8M32 20h8M32 28h8M32 36h8"/></svg></div>
  <h4>Interiors</h4>
  <p>Sed ut perspiciatis unde omnis iste natus error sit voluptatem santium doloremque laudantium</p>
</div>
<div class="feature" style="left:610px">
  <div class="ring"><svg width="52" height="52" viewBox="0 0 52 52" fill="none" stroke="#333" stroke-width="2.5"><path d="M4 26 26 6l22 20M10 22v24h32V22M21 46V32h10v14"/></svg></div>
  <h4>New Residential</h4>
  <p>Sed ut perspiciatis unde omnis iste natus error sit voluptatem santium doloremque laudantium</p>
</div>
<div class="feature" style="left:871px">
  <div class="ring"><svg width="52" height="52" viewBox="0 0 52 52" fill="none" stroke="#333" stroke-width="2.5"><rect x="8" y="8" width="36" height="38"/><path d="M14 16h6M24 16h6M34 16h4M14 24h6M24 24h6M34 24h4M14 32h6M24 32h6M34 32h4M22 46v-8h8v8"/></svg></div>
  <h4>Commercial/Public</h4>
  <p>Sed ut perspiciatis unde omnis iste natus error sit voluptatem santium doloremque laudantium</p>
</div>

<h2 class="section-title" style="top:1516px">LATEST PROJECT</h2>
<div class="title-rule" style="top:1574px"></div>

<div class="photo" role="img" aria-label="Photo of a stone house with pool and patio" style="left:0;top:1624px;width:396px;height:269px;background:linear-gradient(170deg,#8fb2d6 0%,#c9ad86 45%,#4f8a54 100%)"></div>
<div class="photo" role="img" aria-label="Photo of a finished interior project" style="left:402px;top:1624px;width:396px;height:269px;background:linear-gradient(160deg,#6c6660,#3d3935)"></div>
<div class="tile-caption"><p>SED UT PERSPICIATIS UNDE<br>OMNIS ISTE NATUS</p><svg width="26" height="26" viewBox="0 0 26 26"><path d="M13 2v22M2 13h22" stroke="#fff" stroke-width="4"/></svg></div>
<div class="photo" role="img" aria-label="Photo of a lounge with glass chandeliers and wine wall" style="left:805px;top:1624px;width:395px;height:269px;background:linear-gradient(160deg,#a8998a,#5d5248 55%,#cfc2b2)"></div>
<div class="photo" role="img" aria-label="Photo of a bathroom with patterned tile and freestanding tub" style="left:0;top:1900px;width:594px;height:303px;background:linear-gradient(150deg,#ebe8e4,#c7c2bc 50%,#a07a5a)"></div>
<div class="photo" role="img" aria-label="Photo of a bedroom with upholstered headboard" style="left:601px;top:1900px;width:599px;height:303px;background:linear-gradient(150deg,#d2c7bb,#8b766a 55%,#b5a190)"></div>

<h2 class="section-title" style="top:2297px">TESTIMONIALS</h2>
<p class="quote">“ Sed ut perspiciatis unde omnis iste natus error sit voluptatem accusantium doloremque laudantium, totam rem aperiam, eaque ipsa quae ab illo inventore veritatis et quasi architecto beatae vitae dicta sunt explicabo. Nemo enim ipsam voluptatem quia voluptas sit aspernatur aut odit aut fugit, sed quia consequuntur magni dolores eos qui ratione voluptatem ”</p>
<p class="quote-by">Alex Reed - Marlow Designs</p>
<div class="dots"><span class="on"></span><span></span><span></span></div>

<section class="ba" role="img" aria-label="Dark background photo of a house exterior"></section>
<h2 class="section-title" style="top:2645px;color:var(--white)">BEFORE &amp; AFTER</h2>
<div class="title-rule" style="top:2702px;background:var(--white)"></div>
<div class="ba-frame" style="left:211px;width:388px">
  <div class="photo" role="img" aria-label="Photo of a room with sliding door before renovation" style="inset:0;background:linear-gradient(160deg,#b8b2aa,#6d5a4a 60%,#8e2f2a)"></div>
  <span class="ba-tag">BEFORE</span>
</div>
<div class="ba-frame" style="left:599px;width:390px">
  <div class="photo" role="img" aria-label="Photo of the same room with new sliding door after renovation" style="inset:0;background:linear-gradient(160deg,#e3e3e1,#8ea07e 55%,#cdb596)"></div>
  <span class="ba-tag">AFTER</span>
</div>
<div class="arrow" style="left:157px;top:2928px;background:rgba(0,0,0,.8)"><svg width="12" height="14" viewBox="0 0 12 14"><path d="M9 1 3 7l6 6" stroke="#fff" stroke-width="2.2" fill="none"/></svg></div>
<div class="arrow" style="left:1013px;top:2928px;background:rgba(0,0,0,.8)"><svg width="12" height="14" viewBox="0 0 12 14"><path d="M3 1l6 6-6 6" stroke="#fff" stroke-width="2.2" fill="none"/></svg></div>

<section class="contact"></section>
<h3 class="col-title" style="left:97px">CONTACT US</h3>
<div class="info" style="top:3328px"><svg width="14" height="16" viewBox="0 0 14 16"><path d="M7 15S1 9 1 6a6 6 0 0 1 12 0c0 3-6 9-6 9z" fill="#444"/><circle cx="7" cy="6" r="2" fill="#ececec"/></svg><div>Marlow Designs<br>14 Harbour Rd.<br>Cedar Bay, NL B2C 4D7</div></div>
<div class="info" style="top:3398px"><svg width="14" height="14" viewBox="0 0 14 14"><path d="M3 1l2.5 3-1.5 2a8 8 0 0 0 4 4l2-1.5 3 2.5-1.5 2C6 13 1 8 1 2.5z" fill="#444"/></svg><div>Phone:555-210-4471<br>Fax:555-210-4472</div></div>
<div class="info" style="top:3452px"><svg width="14" height="12" viewBox="0 0 14 12"><rect x="1" y="2" width="12" height="8" fill="#444"/><path d="M1 2l6 5 6-5" stroke="#ececec" fill="none"/></svg><div>Email: hello@marlowdesigns.example</div></div>

<h3 class="col-title" style="left:417px">GET A QUICK NOW!</h3>
<div class="field" style="left:417px;top:3330px">Your Name</div>
<div class="field" style="left:657px;top:3330px">Your E - Mail</div>
<div class="field" style="left:417px;top:3384px">Your Phone</div>
<div class="field" style="left:657px;top:3384px">Message</div>
<div class="submit">SUBMIT</div>

<h3 class="col-title" style="left:946px">QUICK LINKS</h3>
<ul class="links"><li>Home</li><li>About Us</li><li>Services</li><li>Projects</li><li>Property Management</li><li>Contact Us</li></ul>

<footer>
  <div class="foot-mark"></div>
  <p class="copy">©2018 Marlow Designs . All Rights Reserved</p>
  <div class="social-foot"><span></span><span></span><span></span><span></span></div>
</footer>

</body>
</html>
```